Caldrift - Where every box finds its place!

Hello,
I'd like to update, re-vamp, and re-tool this current power point presentation with slightly more professional appearance as well as more accurately reflect the website -caldrift.com- color scheme and sleek design scheme. Please see attached.
We at Caldrift pride ourselves on seeking to rework an archaic business into something progressive, cost effective, more reliable, and easily accessible in todays fast growing market that has only gotten more expensive, more costly and less indirect over the last couple years.

Target Market(s)

New updated and hassle free moving opportunities no matter how large or how small in a market that begs for a change

Industry/Entity Type

Logistics/Moving

Requirements
Must have
• The current color scheme from the -caldrift.com- website as well as the inclusion of the current data on the sample power point presentation provided but with updated graphics

```html
<!DOCTYPE html>
<html lang="en">
<head>
<meta charset="utf-8">
<title>Caldrift – Presentation</title>
<link href="https://fonts.googleapis.com/css2?family=Montserrat:wght@500;700;800&family=Open+Sans:wght@400;600&display=swap" rel="stylesheet">
<style>
  :root{
    --blue:#1f50c8;
    --blue-dark:#173e9e;
    --yellow:#f8c51c;
    --yellow-soft:#fff8e1;
    --ink:#2b2f3a;
    --muted:#6b7080;
    --page:#eef0f4;
    --white:#ffffff;
    --photo-warm:#c9b59a;
    --photo-cool:#b9c4d2;
  }
  *{box-sizing:border-box;margin:0;padding:0}
  html,body{width:1200px;height:4048px;overflow:hidden;background:var(--page);font-family:"Open Sans",Arial,sans-serif;color:var(--ink)}
  .deck{position:relative;width:1200px;height:4048px}
  .slide{position:absolute;left:72px;width:1056px;height:594px;background:var(--white);overflow:hidden;box-shadow:0 4px 18px rgba(20,30,60,.12)}
  .slide svg.bg{position:absolute;inset:0}
  .photo{position:absolute}
  .brand{position:absolute;display:flex;align-items:center;gap:10px;font-family:"Montserrat",sans-serif;font-weight:800;font-size:26px}
  .brand .mark{width:22px;height:22px;background:currentColor}
  .brand.blue{color:var(--blue)}
  .brand.white{color:var(--white)}
  h2{font-family:"Montserrat",sans-serif;font-weight:800;font-size:36px;color:var(--blue)}
  h2 .hl{color:var(--yellow)}
  p{font-size:12.5px;line-height:1.65;color:var(--muted)}

  /* cover */
  .cover-title{position:absolute;left:60px;top:210px;font-family:"Montserrat",sans-serif;font-weight:800;font-size:56px;color:var(--white)}
  .cover-sub{position:absolute;left:60px;top:285px;font-family:"Montserrat",sans-serif;font-weight:700;font-size:22px;color:var(--yellow)}
  .cover-web{position:absolute;left:60px;bottom:36px;display:flex;align-items:center;gap:12px;color:var(--white);font-size:14px}
  .ring{width:30px;height:30px;border-radius:50%;border:2px solid var(--white);display:flex;align-items:center;justify-content:center}

  /* about */
  .about-text{position:absolute;left:560px;top:110px;width:440px}
  .about-text h2{margin-bottom:6px}
  .bar{width:70px;height:5px;background:var(--yellow);margin-bottom:22px}
  .about-text p{margin-bottom:14px}

  /* vision */
  .center-title{position:absolute;left:0;right:0;top:44px;text-align:center}
  .cards{position:absolute;left:120px;right:120px;top:170px;display:flex;gap:36px}
  .card{flex:1;height:240px;border:2px solid var(--blue);background:var(--white);position:relative;padding:62px 22px 20px;text-align:center}
  .card.featured{border-color:var(--yellow);background:var(--yellow-soft)}
  .card .badge{position:absolute;left:50%;top:-32px;transform:translateX(-50%);width:64px;height:64px;border-radius:50%;background:var(--blue);border:5px solid var(--white);box-shadow:0 0 0 2px var(--blue);display:flex;align-items:center;justify-content:center}
  .card.featured .badge{background:var(--yellow);box-shadow:0 0 0 2px var(--yellow)}
  .card h3{font-family:"Montserrat",sans-serif;font-size:14px;font-weight:700;color:var(--yellow);margin-bottom:12px}
  .card p{font-size:11.5px;line-height:1.6}

  /* problems */
  .steps{position:absolute;left:70px;right:70px;top:210px;display:flex;gap:26px}
  .step{flex:1;height:170px;background:var(--white);box-shadow:0 3px 12px rgba(20,30,60,.12);border-top:4px solid var(--yellow);position:relative;padding:52px 16px 14px;text-align:center}
  .step .badge{position:absolute;left:50%;top:-26px;transform:translateX(-50%);width:50px;height:50px;border-radius:8px;background:var(--blue);display:flex;align-items:center;justify-content:center}
  .step h3{font-family:"Montserrat",sans-serif;font-size:12px;font-weight:700;color:var(--yellow);margin-bottom:8px}
  .step p{font-size:10.5px;line-height:1.55}

  /* solution */
  .solution-title{position:absolute;left:40px;top:40px}
  .solution-list{position:absolute;left:40px;top:110px;width:440px;list-style:none}
  .solution-list li{display:flex;gap:14px;margin-bottom:20px}
  .solution-list .dot{flex:none;width:36px;height:36px;border-radius:50%;background:var(--blue);display:flex;align-items:center;justify-content:center}
  .solution-list h4{font-family:"Montserrat",sans-serif;font-size:11px;font-weight:700;color:var(--yellow);margin-bottom:3px}
  .solution-list p{font-size:10.5px;line-height:1.5}

  /* thanks */
  .thanks-title{position:absolute;right:40px;top:36px;font-family:"Montserrat",sans-serif;font-weight:800;font-size:48px;color:var(--white)}
  .thanks-title .hl{color:var(--yellow)}
  .contacts{position:absolute;left:560px;top:140px;list-style:none}
  .contacts li{display:flex;align-items:center;gap:16px;color:var(--white);font-size:14px;height:40px;margin-bottom:22px}
  .contacts .dot{flex:none;width:36px;height:36px;border-radius:50%;background:var(--white);display:flex;align-items:center;justify-content:center}
</style>
</head>
<body>
<main class="deck">

  <!-- Slide 1: cover -->
  <section class="slide cover" style="top:80px">
    <div class="photo" role="img" aria-label="Family carrying cardboard moving boxes into a bright living room" style="left:520px;top:0;width:536px;height:594px;background:linear-gradient(135deg,var(--photo-cool),var(--photo-warm))"></div>
    <svg class="bg" width="1056" height="594" viewBox="0 0 1056 594" aria-hidden="true">
      <polygon points="0,0 640,0 450,594 0,594" fill="#1f50c8"/>
      <polygon points="640,0 680,0 490,594 450,594" fill="#f8c51c"/>
    </svg>
    <div class="brand white" style="left:60px;top:40px"><span class="mark"></span>Caldrift</div>
    <div class="cover-title">Caldrift</div>
    <div class="cover-sub">Moving for the next generation</div>
    <div class="cover-web">
      <span class="ring"><svg width="14" height="14" viewBox="0 0 14 14"><circle cx="7" cy="7" r="6" fill="none" stroke="#fff" stroke-width="1.4"/><path d="M1 7h12M7 1c3 3 3 9 0 12M7 1c-3 3-3 9 0 12" fill="none" stroke="#fff" stroke-width="1.2"/></svg></span>
      www.caldrift.com
    </div>
  </section>

  <!-- Slide 2: about -->
  <section class="slide about" style="top:740px">
    <div class="photo" role="img" aria-label="Empty room with stacked moving boxes and a chair" style="left:60px;top:80px;width:440px;height:330px;background:linear-gradient(160deg,#e3ded6,var(--photo-warm))"></div>
    <div class="about-text">
      <h2>About <span class="hl">Us</span></h2>
      <div class="bar"></div>
      <p>Caldrift is the next logical evolution in professional moving. Professional moving clients have battled rising prices, poor capacity, hidden fees and disappointing service for years.</p>
      <p>Caldrift was founded by lifelong moving professionals who have developed the answer to better moving services. Trusted as the industry disruptor, we deliver faster, offer guaranteed prices and even offer on-credit direct financing options. We are a technology first organization using proprietary software to deliver moving's best service experience.</p>
    </div>
    <svg class="bg" width="1056" height="594" viewBox="0 0 1056 594" aria-hidden="true" style="pointer-events:none">
      <polygon points="0,540 760,540 740,566 0,566" fill="#f8c51c"/>
      <rect x="0" y="570" width="740" height="3" fill="#1f50c8"/>
    </svg>
    <div class="brand blue" style="right:40px;bottom:26px;font-size:22px"><span class="mark" style="width:18px;height:18px"></span>Caldrift</div>
  </section>

  <!-- Slide 3: vision -->
  <section class="slide vision" style="top:1400px">
    <h2 class="center-title">Caldrift <span class="hl">Vision</span></h2>
    <div class="cards">
      <div class="card">
        <span class="badge"><svg width="26" height="26" viewBox="0 0 26 26"><path d="M1 13s5-8 12-8 12 8 12 8-5 8-12 8S1 13 1 13z" fill="none" stroke="#fff" stroke-width="2"/><circle cx="13" cy="13" r="4" fill="#fff"/></svg></span>
        <h3>OUR VISION</h3>
        <p>An end to the old days of unfair pricing and damaged goods. Caldrift strives to become the most trusted name in moving, pairing skilled crews with smart technology and honest, transparent service.</p>
      </div>
      <div class="card featured">
        <span class="badge"><svg width="26" height="26" viewBox="0 0 26 26"><circle cx="13" cy="13" r="11" fill="none" stroke="#fff" stroke-width="2"/><circle cx="13" cy="13" r="6" fill="none" stroke="#fff" stroke-width="2"/><circle cx="13" cy="13" r="2" fill="#fff"/></svg></span>
        <h3>OUR MISSION</h3>
        <p>Our goal is to bring a peace of mind to every client. Caldrift delivers careful handling and a professional crew, supported by fair pricing and flexible payment, so every move ends with a smile.</p>
      </div>
      <div class="card">
        <span class="badge"><svg width="26" height="26" viewBox="0 0 26 26"><path d="M6 24V3M6 4h14l-4 5 4 5H6" fill="none" stroke="#fff" stroke-width="2" stroke-linejoin="round"/></svg></span>
        <h3>OUR GOAL</h3>
        <p>Removing the moving problems of today. We intend to reach every home, grow the customer base and make each household move simple, affordable and stress free, one box at a time.</p>
      </div>
    </div>
    <svg class="bg" width="1056" height="594" viewBox="0 0 1056 594" aria-hidden="true" style="pointer-events:none">
      <polygon points="0,548 780,548 760,574 0,574" fill="#f8c51c"/>
    </svg>
    <div class="brand blue" style="right:40px;bottom:22px;font-size:22px"><span class="mark" style="width:18px;height:18px"></span>Caldrift</div>
  </section>

  <!-- Slide 4: problems -->
  <section class="slide problems" style="top:2060px">
    <h2 class="center-title">Moving's <span class="hl">Problems</span></h2>
    <svg class="bg" width="1056" height="594" viewBox="0 0 1056 594" aria-hidden="true">
      <path d="M300 190 C 380 120, 600 110, 700 170" fill="none" stroke="#c9cdd6" stroke-width="8"/>
      <polygon points="700,158 722,182 694,186" fill="#c9cdd6"/>
      <path d="M170 420 C 220 470, 330 470, 380 430" fill="none" stroke="#c9cdd6" stroke-width="8"/>
      <polygon points="372,420 396,424 382,446" fill="#c9cdd6"/>
      <path d="M660 420 C 710 470, 820 470, 870 430" fill="none" stroke="#c9cdd6" stroke-width="8"/>
      <polygon points="862,420 886,424 872,446" fill="#c9cdd6"/>
      <polygon points="0,548 780,548 760,574 0,574" fill="#f8c51c"/>
    </svg>
    <div class="steps">
      <div class="step">
        <span class="badge"><svg width="24" height="24" viewBox="0 0 24 24"><circle cx="12" cy="12" r="10" fill="none" stroke="#fff" stroke-width="2"/><text x="12" y="17" text-anchor="middle" fill="#fff" font-size="13" font-family="Montserrat,sans-serif" font-weight="700">$</text></svg></span>
        <h3>COST</h3>
        <p>Moving cost has skyrocketed over the last three years. Charges have increased over 35% since 2019.</p>
      </div>
      <div class="step">
        <span class="badge"><svg width="24" height="24" viewBox="0 0 24 24"><rect x="2" y="6" width="20" height="14" fill="none" stroke="#fff" stroke-width="2"/><path d="M2 11h20M12 6v5" stroke="#fff" stroke-width="2"/></svg></span>
        <h3>CAPACITY</h3>
        <p>Long lead times, damages and limited equipment. Crews are still growing demand has pushed capacity to a critical state.</p>
      </div>
      <div class="step">
        <span class="badge"><svg width="24" height="24" viewBox="0 0 24 24"><circle cx="12" cy="8" r="4" fill="none" stroke="#fff" stroke-width="2"/><path d="M4 22c0-5 4-8 8-8s8 3 8 8" fill="none" stroke="#fff" stroke-width="2"/></svg></span>
        <h3>SERVICE</h3>
        <p>Quality labor has been difficult to source and retain. Customer reviews across the field show a steady decline in service quality.</p>
      </div>
      <div class="step">
        <span class="badge"><svg width="24" height="24" viewBox="0 0 24 24"><circle cx="10" cy="10" r="7" fill="none" stroke="#fff" stroke-width="2"/><path d="M15 15l7 7" stroke="#fff" stroke-width="2.4"/></svg></span>
        <h3>TRANSPARENCY</h3>
        <p>Too many hidden clauses and fees. Old style quotes lead to surprise charges and stressful, confusing moving days.</p>
      </div>
    </div>
    <div class="brand blue" style="right:40px;bottom:22px;font-size:22px"><span class="mark" style="width:18px;height:18px"></span>Caldrift</div>
  </section>

  <!-- Slide 5: solution -->
  <section class="slide solution" style="top:2720px">
    <div class="photo" role="img" aria-label="Happy woman stretching on a floor among moving boxes in a new home" style="left:620px;top:0;width:436px;height:594px;background:linear-gradient(150deg,#dcd6cc,var(--photo-warm))"></div>
    <svg class="bg" width="1056" height="594" viewBox="0 0 1056 594" aria-hidden="true">
      <polygon points="620,0 900,0 620,594 520,594 520,300" fill="#ffffff"/>
      <polygon points="880,0 920,0 640,594 600,594" fill="#1f50c8"/>
      <polygon points="920,0 936,0 656,594 640,594" fill="#f8c51c"/>
      <polygon points="0,520 520,520 505,540 0,540" fill="#f8c51c"/>
    </svg>
    <h2 class="solution-title">Our <span class="hl">Solution</span></h2>
    <ul class="solution-list">
      <li><span class="dot"><svg width="18" height="18" viewBox="0 0 18 18"><path d="M3 9l4 4 8-8" fill="none" stroke="#fff" stroke-width="2.2"/></svg></span><div><h4>VERIFIED PRICING</h4><p>Upfront prices locked at booking. No hidden fees, no surprises, just clear honest quotes for every move.</p></div></li>
      <li><span class="dot"><svg width="18" height="18" viewBox="0 0 18 18"><circle cx="9" cy="6" r="3" fill="#fff"/><path d="M3 16c0-4 3-6 6-6s6 2 6 6" fill="#fff"/></svg></span><div><h4>ONE POINT OF CONTACT</h4><p>A dedicated move manager guides you from first call to final box, always ready to answer questions.</p></div></li>
      <li><span class="dot"><svg width="18" height="18" viewBox="0 0 18 18"><rect x="2" y="6" width="14" height="9" fill="none" stroke="#fff" stroke-width="2"/><path d="M6 6V3h6v3" fill="none" stroke="#fff" stroke-width="2"/></svg></span><div><h4>GUARANTEED DATES</h4><p>Reserved crews and trucks mean your moving date stays your moving date, backed by our on-time promise.</p></div></li>
      <li><span class="dot"><svg width="18" height="18" viewBox="0 0 18 18"><path d="M9 1a5 5 0 015 5c0 4-5 10-5 10S4 10 4 6a5 5 0 015-5z" fill="#fff"/></svg></span><div><h4>GPS TRACKING</h4><p>Follow your belongings live in our app, with real-time updates from pickup through delivery.</p></div></li>
      <li><span class="dot"><svg width="18" height="18" viewBox="0 0 18 18"><rect x="2" y="4" width="14" height="10" rx="1" fill="none" stroke="#fff" stroke-width="2"/><path d="M2 8h14" stroke="#fff" stroke-width="2"/></svg></span><div><h4>DIRECT FINANCING</h4><p>Flexible on-credit payment plans make any move affordable, with quick approval and clear terms.</p></div></li>
    </ul>
    <div class="brand blue" style="left:40px;bottom:20px;font-size:22px"><span class="mark" style="width:18px;height:18px"></span>Caldrift</div>
  </section>

  <!-- Slide 6: thank you -->
  <section class="slide thanks" style="top:3380px">
    <div class="photo" role="img" aria-label="Mover in blue uniform taping a cardboard box" style="left:0;top:0;width:560px;height:594px;background:linear-gradient(140deg,var(--photo-cool),#8ea4c8)"></div>
    <svg class="bg" width="1056" height="594" viewBox="0 0 1056 594" aria-hidden="true">
      <polygon points="470,0 1056,0 1056,594 340,594" fill="#1f50c8"/>
      <polygon points="430,0 470,0 340,594 300,594" fill="#f8c51c"/>
      <polygon points="760,594 1056,440 1056,594" fill="#f8c51c"/>
    </svg>
    <div class="thanks-title">THANK <span class="hl">YOU!</span></div>
    <ul class="contacts">
      <li><span class="dot"><svg width="16" height="16" viewBox="0 0 18 18"><path d="M9 1a5 5 0 015 5c0 4-5 10-5 10S4 10 4 6a5 5 0 015-5z" fill="#1f50c8"/></svg></span><span>4170 Harbor Lane<br>Tulsa Ridge, OK 74010</span></li>
      <li><span class="dot"><svg width="16" height="16" viewBox="0 0 18 18"><path d="M4 1l3 4-2 2c1 3 3 5 6 6l2-2 4 3-2 3C8 17 1 10 1 3z" fill="#1f50c8"/></svg></span><span>(800) 555-0142</span></li>
      <li><span class="dot"><svg width="16" height="16" viewBox="0 0 14 14"><circle cx="7" cy="7" r="6" fill="none" stroke="#1f50c8" stroke-width="1.4"/><path d="M1 7h12M7 1c3 3 3 9 0 12M7 1c-3 3-3 9 0 12" fill="none" stroke="#1f50c8" stroke-width="1.2"/></svg></span><span>www.caldrift.com</span></li>
      <li><span class="dot"><svg width="16" height="16" viewBox="0 0 18 18"><rect x="1" y="4" width="16" height="11" fill="none" stroke="#1f50c8" stroke-width="1.8"/><path d="M1 4l8 6 8-6" fill="none" stroke="#1f50c8" stroke-width="1.8"/></svg></span><span>support@caldrift.com</span></li>
    </ul>
    <div class="brand white" style="right:40px;bottom:22px;font-size:22px"><span class="mark" style="width:18px;height:18px"></span>Caldrift</div>
  </section>

</main>
</body>
</html>
```